Glimmora.ca Website Build For costume embellishment service

Design a website to promote our business.
Costume embellishing services for Artistic Swimming, Dance, Skating, Gymnastics etc.
We add sparkle to costumes using Kelvarne and Lumetta crystals to plain costumes that our customers provide. We also sell new costumes already decorated, Lastly we specialize in reimagining costumes to make them look like new.
We would like samples of our work to be displayed in pictures and video.
We need an information about our services page as well as a contact us page. We have a logo for Glimmora which is pink. We like a modern aesthetic as well as bright colours. We are hoping to promote our services worldwide but a big push for Canada. We need to convey that we are Canadian. We would like help with writing copy as well.
We currently have a cartwell webpage glimmora.ca but would like to shut down the cartwell site as we don't need the payment service. In the new website we will promote payment by PayRoam or transfer.
A copy of our logo is attached.

Target Market(s)

Athletes and Dancers under 18 years old and parents

Industry/Entity Type

costume embellishment service

Coding

Coded - Design and coding required

Number of Pages Required

4 page

Font styles to use
Sans Serif
Other font styles liked:
• match to the logo for titles

Colors
E54698
E96AAD
F1A4CE
F9D9EA
FCEFF6

Requirements
Must have
• Photos and video upload capability there will be allot of before and after pictures as well as unclose videos.
Nice to have
• modern look I like the look of this website http://www.bramblecloset-example.com
Should not have
• not busy looking

```html
<!DOCTYPE html>
<html lang="en">
<head>
<meta charset="utf-8">
<title>Glimmora – Costume Embellishment</title>
<link rel="stylesheet" href="https://fonts.googleapis.com/css2?family=Roboto:wght@400;500;700&family=Yellowtail&display=swap">
<style>
  :root {
    --magenta: #c0077a;
    --magenta-dark: #a5066a;
    --pink: #e54698;
    --pink-mid: #e96aad;
    --pink-soft: #f1a4ce;
    --blush: #f9d9ea;
    --blush-light: #fceff6;
    --ink: #222222;
    --text: #555555;
    --white: #ffffff;
    --script: "Yellowtail", cursive;
    --sans: "Roboto", Arial, sans-serif;
  }
  * { box-sizing: border-box; margin: 0; padding: 0; }
  html, body { width: 1200px; height: 4376px; overflow: hidden; }
  body { position: relative; font-family: var(--sans); color: var(--text); background: var(--white); }
  .abs { position: absolute; }

  /* Header */
  .site-header { left: 0; top: 0; width: 1200px; height: 98px; background: var(--magenta); }
  .brand { left: 110px; top: 26px; font-family: var(--script); font-size: 42px; color: var(--white); line-height: 1; white-space: nowrap; }
  .main-nav a { position: absolute; top: 39px; color: var(--white); font-size: 15px; font-weight: 700; text-decoration: none; letter-spacing: .2px; }
  .inquiry-icon { left: 924px; top: 31px; width: 36px; height: 36px; border-radius: 50%; background: var(--white); }
  .inquiry-label { left: 970px; top: 29px; color: var(--white); font-size: 12px; }
  .inquiry-mail { left: 970px; top: 49px; color: var(--white); font-size: 15px; font-weight: 700; }

  /* Hero */
  .hero-photo { left: 0; top: 98px; width: 1200px; height: 589px; background: linear-gradient(120deg, #5cc8ef 0%, #2aa3dd 45%, #1c6fb0 75%, #123d7a 100%); }
  .hero-brand { left: 110px; top: 262px; font-family: var(--script); font-size: 72px; color: var(--white); line-height: 1; white-space: nowrap; }
  .hero-tagline { left: 112px; top: 378px; width: 340px; color: var(--white); font-size: 14px; font-weight: 700; line-height: 26px; }
  .btn { display: flex; align-items: center; justify-content: center; border-radius: 30px; font-size: 15px; font-weight: 700; text-decoration: none; text-transform: uppercase; white-space: nowrap; }
  .btn.abs, a.abs { position: absolute; }
  .btn-primary { background: var(--magenta); color: var(--white); }
  .btn-light { background: var(--white); color: var(--magenta); }

  /* Titles */
  .section-title { font-family: var(--script); color: var(--magenta); font-size: 44px; line-height: 1.1; font-weight: 400; white-space: nowrap; }
  .section-title.abs { position: absolute; }
  .center { left: 0; width: 1200px; text-align: center; }
  .welcome-lead { top: 824px; color: var(--ink); font-size: 14px; font-weight: 500; }
  .welcome-text { font-size: 15px; }
  .welcome-small { font-size: 13px; }
  .sport { position: absolute; top: 956px; width: 200px; text-align: center; }
  .sport-badge { display: block; width: 112px; height: 112px; margin: 0 auto; }
  .sport-name { margin-top: 18px; color: var(--ink); font-size: 17px; font-weight: 500; }

  /* Feature blocks */
  .photo, .panel { position: absolute; }
  .feature { position: absolute; }
  .feature .section-title { font-size: 38px; margin-bottom: 18px; }
  .feature-copy { font-size: 14px; line-height: 26px; color: var(--text); }
  .feature-copy p { margin-bottom: 7px; }
  .feature .btn { margin-top: 26px; }
  .accent { color: var(--magenta); font-weight: 700; }
  .price { color: var(--magenta); font-weight: 700; font-size: 17px; }
  .mail-link { color: var(--magenta); font-weight: 500; text-decoration: underline; }

  /* Purchase band */
  .purchase-band { left: 0; top: 2768px; width: 1200px; height: 270px; background: var(--pink-mid); }

  /* Gallery */
  .tile { position: absolute; }
  .play { position: absolute; width: 56px; height: 56px; border-radius: 50%; background: var(--magenta); }

  /* Footer */
  .site-footer { left: 0; top: 3963px; width: 1200px; height: 357px; background: var(--magenta); }
  .footer-brand { left: 116px; top: 4122px; font-family: var(--script); font-size: 50px; color: var(--white); line-height: 1; white-space: nowrap; }
  .footer-heading { position: absolute; top: 4032px; color: var(--white); font-size: 18px; font-weight: 700; white-space: nowrap; }
  .footer-rule { position: absolute; top: 4068px; width: 64px; height: 2px; background: var(--pink-soft); }
  .footer-link { position: absolute; color: var(--white); font-size: 12px; text-decoration: none; }
  .footer-text { position: absolute; color: var(--white); font-size: 12px; line-height: 17px; }
  .subscribe-box { left: 838px; top: 4145px; width: 250px; height: 34px; border-radius: 17px; background: var(--white); overflow: hidden; }
  .subscribe-box span { position: absolute; left: 26px; top: 10px; font-size: 11px; color: #888; }
  .subscribe-send { position: absolute; right: 0; top: 0; width: 48px; height: 34px; background: var(--pink-mid); }
  .social { position: absolute; top: 4201px; width: 30px; height: 30px; border-radius: 50%; background: var(--white); }
  .bottom-bar { left: 0; top: 4320px; width: 1200px; height: 56px; background: var(--magenta-dark); }
  .bottom-text { position: absolute; top: 4341px; color: var(--white); font-size: 13px; white-space: nowrap; }
  .bottom-text a { color: var(--white); }
</style>
</head>
<body>

<!-- Header -->
<header class="abs site-header"></header>
<div class="abs brand">Glimmora</div>
<nav class="main-nav">
  <a href="#" style="left:404px">HOME</a>
  <a href="#" style="left:486px">IMAGES</a>
  <a href="#" style="left:581px">ABOUT US</a>
  <a href="#" style="left:694px">SHIPPING FAQ</a>
</nav>
<div class="abs inquiry-icon">
  <svg width="36" height="36" viewBox="0 0 36 36"><rect x="10" y="12" width="16" height="12" rx="1.5" fill="var(--magenta)"/><path d="M10.5 13 L18 19 L25.5 13" fill="none" stroke="#fff" stroke-width="1.6"/></svg>
</div>
<div class="abs inquiry-label">Send all inquires</div>
<div class="abs inquiry-mail">info@glimmora.ca</div>

<!-- Hero -->
<div class="abs hero-photo" role="img" aria-label="Swimmer in a navy cap and suit gliding through bright blue pool water"></div>
<div class="abs hero-brand">Glimmora</div>
<p class="abs hero-tagline">Dazzling competition suits and costumes for all sports and events</p>
<a href="#" class="btn btn-primary abs" style="left:112px;top:452px;width:172px;height:45px">Shop Now
  <svg width="14" height="14" viewBox="0 0 14 14" style="margin-left:7px"><circle cx="7" cy="7" r="7" fill="#fff"/><path d="M5.5 4 L8.5 7 L5.5 10" fill="none" stroke="var(--magenta)" stroke-width="1.8"/></svg>
</a>

<!-- Welcome -->
<h2 class="section-title abs center" style="top:746px">Welcome To Glimmora</h2>
<p class="abs center welcome-lead">Dazzling competition suits and costumes for all sports and events</p>
<p class="abs center welcome-text" style="top:851px">Create a Dazzling new costume or restyle an existing favourite... no job is too big or too small.</p>
<p class="abs center welcome-small" style="top:885px">Our master costume applique designer will work closely with you to fully understand your needs before starting any project.</p>
<p class="abs center welcome-small" style="top:910px">Your satisfaction is our ultimate goal.</p>

<div class="sport" style="left:177px">
  <svg class="sport-badge" viewBox="0 0 112 112" role="img" aria-label="Artistic swimming pictogram"><rect x="18" y="18" width="76" height="76" rx="8" transform="rotate(45 56 56)" fill="var(--magenta)"/></svg>
  <div class="sport-name">Artistic Swimming</div>
</div>
<div class="sport" style="left:398px">
  <svg class="sport-badge" viewBox="0 0 112 112" role="img" aria-label="Dance pictogram"><rect x="18" y="18" width="76" height="76" rx="8" transform="rotate(45 56 56)" fill="var(--magenta)"/></svg>
  <div class="sport-name">Dance</div>
</div>
<div class="sport" style="left:617px">
  <svg class="sport-badge" viewBox="0 0 112 112" role="img" aria-label="Gymnastics pictogram"><rect x="18" y="18" width="76" height="76" rx="8" transform="rotate(45 56 56)" fill="var(--magenta)"/></svg>
  <div class="sport-name">Gymnastics</div>
</div>
<div class="sport" style="left:837px">
  <svg class="sport-badge" viewBox="0 0 112 112" role="img" aria-label="Skating pictogram"><rect x="18" y="18" width="76" height="76" rx="8" transform="rotate(45 56 56)" fill="var(--magenta)"/></svg>
  <div class="sport-name">Skating</div>
</div>

<!-- Original Costume Embellishment -->
<div class="photo" style="left:0;top:1197px;width:600px;height:461px;background:linear-gradient(160deg,#2c2a4a 0%,#7a2a6a 45%,#d23c9a 65%,#3a2030 100%)" role="img" aria-label="Dance troupe posing on stage in pink embellished costumes"></div>
<div class="panel" style="left:600px;top:1197px;width:600px;height:461px;background:var(--blush)"></div>
<div class="feature" style="left:658px;top:1258px;width:470px">
  <h2 class="section-title">Original Costume Embellishment</h2>
  <div class="feature-copy">
    <p>Our specialty is design and application, we do not alter the dimensions of the costume or provide any seamstress services.</p>
    <p>Provide the blank canvas (uniform/costume) and we work together on colours, patterns and design.</p>
    <p>We can personalize your swimsuit or costume, by adding Kelvarne or Lumetta rhinestones, sequins and embellishments. We can help create that <span class="accent">WOW Factor!</span></p>
  </div>
  <a href="#" class="btn btn-primary" style="width:153px;height:43px;font-size:14px;margin-top:20px">Our Imges</a>
</div>

<!-- How it works -->
<div class="feature" style="left:110px;top:1814px;width:470px">
  <h2 class="section-title">Here's how it works</h2>
  <div class="feature-copy">
    <p>To start an online consultation, send us a pic of the outfit you want blinged out and we'll get started making colour recommendations and lots of other ideas to get you the result you want.</p>
    <p>We'll document the process step by step and we will not be happy until you are!</p>
    <p>Custom Glimmora application starts at <span class="price">$150 per item.</span></p>
    <p>Upon agreement, send us your outfit and we'll take care of the rest. You can keep track with our progress with shared photos and videos. Upon completion we send back your completed masterpiece. It's that easy!</p>
    <p>Simply contact us for a no cost consultation by email <span class="mail-link">info@glimmora.ca</span></p>
  </div>
</div>
<div class="photo" style="left:614px;top:1768px;width:474px;height:464px;border-radius:8px;background:linear-gradient(180deg,#e8e2dc 0%,#d8d2cc 60%,#9a9aa2 100%)" role="img" aria-label="Two young gymnasts in teal and pink leotards bending on a gym floor"></div>

<!-- Costume revitalizing -->
<div class="photo" style="left:0;top:2346px;width:600px;height:422px;background:linear-gradient(180deg,#eef2f6 0%,#dfe6ee 60%,#c9d3dd 100%)" role="img" aria-label="Two speed skaters in blue and black suits racing on ice"></div>
<div class="panel" style="left:600px;top:2346px;width:600px;height:422px;background:var(--blush-light)"></div>
<div class="feature" style="left:675px;top:2425px;width:420px">
  <h2 class="section-title">Costume revitalizing</h2>
  <div class="feature-copy">
    <p>Restyle or refresh an existing embellished costume by adding new stones to redesign the look. We can also replace missing stones and breathe new life tired or worn outfits. A great option for clubs to inexpensively rejuvenate existing inventory.</p>
  </div>
  <a href="#" class="btn btn-primary" style="width:212px;height:44px;font-size:14px;margin-top:26px">Revitalizing Images</a>
</div>

<!-- Purchase band -->
<section class="abs purchase-band"></section>
<h2 class="section-title abs center" style="top:2830px;color:var(--white);font-size:42px">Purchase a ready to wear costume</h2>
<p class="abs center" style="top:2896px;color:var(--white);font-size:15px">Choose from our inventory of completed costumes.</p>
<a href="#" class="btn btn-light abs" style="left:529px;top:2934px;width:178px;height:42px;font-size:14px">Wear Imges</a>

<!-- Before After gallery -->
<h2 class="section-title abs center" style="top:3110px;font-size:42px">Before After</h2>
<div class="tile" style="left:146px;top:3196px;width:452px;height:318px;background:linear-gradient(180deg,#1a6fc0,#0d3f86)" role="img" aria-label="Underwater view of a swimmer in a patterned suit"></div>
<div class="play" style="left:344px;top:3327px"><svg width="56" height="56" viewBox="0 0 56 56"><path d="M22 17 L40 28 L22 39 Z" fill="#fff"/></svg></div>
<div class="tile" style="left:619px;top:3196px;width:168px;height:318px;background:linear-gradient(180deg,#6fb3e6,#9ccbe2 70%,#d6c4a6)" role="img" aria-label="Woman in a black swimsuit standing by a pool"></div>
<div class="tile" style="left:806px;top:3196px;width:248px;height:140px;background:linear-gradient(180deg,#4a3a30,#8a7a6a)" role="img" aria-label="Gymnast performing a leap on a balance beam"></div>
<div class="tile" style="left:806px;top:3356px;width:248px;height:158px;background:linear-gradient(180deg,#7fb6de,#4a88c0 60%,#d9cdb4)" role="img" aria-label="Man running on a beach in yellow shorts"></div>
<div class="tile" style="left:146px;top:3534px;width:167px;height:318px;background:linear-gradient(180deg,#2a2422,#5a4a40)" role="img" aria-label="Ballroom couple dancing in dark attire"></div>
<div class="tile" style="left:333px;top:3534px;width:247px;height:140px;background:linear-gradient(180deg,#0e1420,#3a4660)" role="img" aria-label="Dancer in motion on a dark stage"></div>
<div class="tile" style="left:333px;top:3694px;width:247px;height:158px;background:linear-gradient(180deg,#141a3a,#4a4a7a 70%,#8a5a3a)" role="img" aria-label="Gymnast on a balance beam in an arena"></div>
<div class="tile" style="left:600px;top:3534px;width:454px;height:318px;background:linear-gradient(180deg,#1a2a4a,#3a5a8a 60%,#5a4a3a)" role="img" aria-label="Latin dance couple performing on a lit stage"></div>
<div class="play" style="left:799px;top:3665px"><svg width="56" height="56" viewBox="0 0 56 56"><path d="M22 17 L40 28 L22 39 Z" fill="#fff"/></svg></div>

<!-- Footer -->
<footer class="abs site-footer"></footer>
<div class="abs footer-brand">Glimmora</div>

<h3 class="footer-heading" style="left:369px">QUICK LINKS</h3>
<div class="footer-rule" style="left:369px"></div>
<a href="#" class="footer-link" style="left:375px;top:4090px">Home</a>
<a href="#" class="footer-link" style="left:375px;top:4116px">Images</a>
<a href="#" class="footer-link" style="left:375px;top:4141px">Services</a>
<a href="#" class="footer-link" style="left:375px;top:4167px">About Us</a>
<a href="#" class="footer-link" style="left:375px;top:4192px">Shipping FAQ</a>

<h3 class="footer-heading" style="left:546px">CONTACT US</h3>
<div class="footer-rule" style="left:546px"></div>
<svg class="abs" style="left:546px;top:4099px" width="14" height="14" viewBox="0 0 14 14"><path d="M3 1 L5.5 1 L6.5 4 L5 5.2 C5.8 7 7 8.2 8.8 9 L10 7.5 L13 8.5 L13 11 C13 12 12 13 11 13 C5.5 12.5 1.5 8.5 1 3 C1 2 2 1 3 1 Z" fill="#fff"/></svg>
<span class="footer-text" style="left:576px;top:4098px">0400 555 019</span>
<svg class="abs" style="left:546px;top:4140px" width="14" height="14" viewBox="0 0 14 14"><rect x="1" y="3" width="12" height="9" rx="1" fill="#fff"/><path d="M1.5 3.5 L7 8 L12.5 3.5" fill="none" stroke="var(--magenta)" stroke-width="1.2"/></svg>
<span class="footer-text" style="left:576px;top:4138px">info@glimmora.ca</span>
<svg class="abs" style="left:547px;top:4180px" width="12" height="16" viewBox="0 0 12 16"><path d="M6 0 C2.7 0 0 2.6 0 5.8 C0 10 6 16 6 16 C6 16 12 10 12 5.8 C12 2.6 9.3 0 6 0 Z" fill="#fff"/><circle cx="6" cy="5.8" r="2.2" fill="var(--magenta)"/></svg>
<span class="footer-text" style="left:576px;top:4178px;width:230px">Lorem ipsum dolor sit amet, adipiscing elit, sed do eiusmod tempor</span>
<svg class="abs" style="left:546px;top:4233px" width="14" height="14" viewBox="0 0 14 14"><rect x="1" y="4" width="12" height="9" rx="1" fill="#fff"/><rect x="3.5" y="1" width="7" height="4" fill="#fff"/><rect x="3.5" y="7" width="7" height="1.4" fill="var(--magenta)"/></svg>
<span class="footer-text" style="left:576px;top:4232px">555-010-7890</span>

<h3 class="footer-heading" style="left:831px">SUBSCRIBE TO OUR BLOG</h3>
<div class="footer-rule" style="left:831px"></div>
<p class="footer-text" style="left:838px;top:4089px;width:250px">Sign up today to get resources on how to attract and retain more customers!</p>
<div class="abs subscribe-box">
  <svg class="abs" style="left:12px;top:12px" width="11" height="9" viewBox="0 0 11 9"><rect x=".5" y=".5" width="10" height="8" fill="none" stroke="#888"/><path d="M.5 .5 L5.5 5 L10.5 .5" fill="none" stroke="#888"/></svg>
  <span>Email Address</span>
  <div class="subscribe-send"><svg width="48" height="34" viewBox="0 0 48 34"><path d="M16 17 L32 10 L27 25 L23 19 Z" fill="#fff"/></svg></div>
</div>
<div class="social" style="left:833px" role="img" aria-label="Social profile"></div>
<div class="social" style="left:872px" role="img" aria-label="Social profile"></div>
<div class="social" style="left:911px" role="img" aria-label="Social profile"></div>
<div class="social" style="left:951px" role="img" aria-label="Social profile"></div>

<div class="abs bottom-bar"></div>
<p class="bottom-text" style="left:110px">Copyright© 2021 <a href="#">glimmora</a> | All Rights Reserved</p>
<p class="bottom-text" style="left:844px">Terms and Conditions &nbsp;| &nbsp;Privacy Policy</p>

</body>
</html>
```